Pierlend- Varno Ridgeway Car Wrap Using Branding and Logo

We need to take our logo and branding and wrap a 2016 Varno Ridgeway. See pierlend.example for more info. This vehicle will be used by the sales and marketing teams to visit boat shows, docks, and boat ramps. Ple

Target Market(s)

Target Market is Boaters and Dock/Boat Slip Owners

Industry/Entity Type

Boating, Docks, Marina

Font styles to use
Serif
Other font styles liked:
• Our font

Colors
0054AA
0677BA
7BADD7
CADEEF
E8F1F8
FFC000
F8CF3A
FAE287
FDF2CF
FEFAEE

Requirements
Must have
• Logo, email, phone, pierlend.example, company brand, picture of a dock with a boat on it
Nice to have
• Like to see some creative, eye catching but clear designs

```html
<!DOCTYPE html>
<html lang="en">
<head>
<meta charset="utf-8">
<title>Pierlend – Vehicle Wrap Side Panel</title>
<link rel="stylesheet" href="https://fonts.googleapis.com/css2?family=Roboto+Slab:wght@800&family=Roboto:wght@400&display=swap">
<style>
  :root {
    --navy: #0e3a4a;
    --orange: #f6a21e;
    --sand-light: #fde6bd;
    --sand: #f8cb7c;
    --ring: #2b2b2b;
    --ink: #111111;
    --white: #ffffff;
    --plank: #efe9d4;
    --dot: #f2ead2;
  }
  * { margin: 0; padding: 0; box-sizing: border-box; }
  html, body { width: 1200px; height: 429px; overflow: hidden; background: var(--white); }
  .wrap-panel { position: relative; width: 1200px; height: 429px; overflow: hidden; background: var(--white); }
  .artwork { position: absolute; inset: 0; }

  .brand { position: absolute; left: 30px; top: 27px; display: flex; align-items: center; gap: 14px; }
  .brand-mark { width: 48px; height: 48px; border-radius: 50%; background: var(--navy); }
  .brand-name {
    font-family: "Roboto Slab", Georgia, serif;
    font-weight: 800;
    font-size: 33px;
    letter-spacing: 1px;
    font-variant: small-caps;
    color: var(--navy);
    line-height: 1;
  }

  .contact {
    position: absolute; left: 152px; width: 283px; height: 67px;
    background: var(--orange);
    display: flex; align-items: center;
    padding-left: 22px; gap: 20px;
    font-family: "Roboto", Arial, sans-serif;
    font-size: 19px; color: var(--ink);
  }
  .contact-email { top: 139px; }
  .contact-phone { top: 233px; }
  .contact-icon { width: 30px; height: 30px; flex: none; }
</style>
</head>
<body>
<div class="wrap-panel">
  <svg class="artwork" viewBox="0 0 1200 429" width="1200" height="429" xmlns="http://www.w3.org/2000/svg">
    <defs>
      <linearGradient id="lake-day" x1="0" y1="0" x2="0" y2="1">
        <stop offset="0" stop-color="#3d8fd6"/><stop offset="0.5" stop-color="#4c7a4a"/><stop offset="1" stop-color="#9a7b5c"/>
      </linearGradient>
      <linearGradient id="lake-dusk" x1="0" y1="0" x2="0" y2="1">
        <stop offset="0" stop-color="#d9c9a8"/><stop offset="0.45" stop-color="#f0a764"/><stop offset="1" stop-color="#6b5a4a"/>
      </linearGradient>
      <linearGradient id="marina-blue" x1="0" y1="0" x2="0" y2="1">
        <stop offset="0" stop-color="#2c86e0"/><stop offset="0.45" stop-color="#cfe3ef"/><stop offset="1" stop-color="#1ba4d9"/>
      </linearGradient>
      <linearGradient id="shore-green" x1="0" y1="0" x2="0" y2="1">
        <stop offset="0" stop-color="#4f8a3a"/><stop offset="0.6" stop-color="#7f8f4a"/><stop offset="1" stop-color="#6f8a3e"/>
      </linearGradient>
      <linearGradient id="open-water" x1="0" y1="0" x2="0" y2="1">
        <stop offset="0" stop-color="#1a55c4"/><stop offset="0.55" stop-color="#4a86d8"/><stop offset="1" stop-color="#3d6e99"/>
      </linearGradient>
      <linearGradient id="palm-pier" x1="0" y1="0" x2="0" y2="1">
        <stop offset="0" stop-color="#6fa6e0"/><stop offset="0.6" stop-color="#b8c9cf"/><stop offset="1" stop-color="#8a6a3e"/>
      </linearGradient>
    </defs>

    <!-- wave bands and water panel -->
    <path class="band-outer" fill="var(--sand-light)" d="M585 0 C548 60 548 120 575 165 C600 205 605 240 603 290 C601 330 592 350 586 361 L1200 361 L1200 0 Z"/>
    <path class="band-inner" fill="var(--sand)" d="M596 0 C566 60 566 120 592 165 C616 205 620 240 618 290 C616 330 610 350 606 361 L1200 361 L1200 0 Z"/>
    <path class="water-panel" fill="var(--navy)" d="M607 0 C582 60 582 120 608 165 C632 205 636 240 634 290 C632 330 627 350 623 361 L1200 361 L1200 0 Z"/>

    <!-- dock planks -->
    <rect class="plank" x="596" y="101" width="57" height="11" fill="var(--plank)"/>
    <rect class="plank" x="634" y="235" width="19" height="11" fill="var(--plank)"/>

    <!-- buoy dots -->
    <g class="buoys" fill="var(--dot)">
      <circle cx="681" cy="39" r="5.5"/><circle cx="681" cy="106" r="5.5"/>
      <circle cx="681" cy="173" r="5.5"/><circle cx="681" cy="241" r="5.5"/>
      <circle cx="681" cy="308" r="5.5"/>
    </g>

    <!-- boat illustrations placeholders -->
    <g class="boats">
      <rect x="606" y="0" width="55" height="12" rx="6" fill="#e3e6e4" role="img" aria-label="Top view of a paddleboard"/>
      <rect x="598" y="56" width="92" height="31" rx="15" fill="#b7c7bf" role="img" aria-label="Top view of a red and white speedboat"/>
      <rect x="606" y="130" width="80" height="25" rx="12" fill="#c3d2cc" role="img" aria-label="Top view of a grey motorboat"/>
      <rect x="627" y="190" width="60" height="25" rx="12" fill="#f1efe6" role="img" aria-label="Top view of a white cruiser"/>
      <rect x="634" y="262" width="70" height="28" rx="13" fill="#bfe2e3" role="img" aria-label="Top view of a sailboat"/>
      <rect x="628" y="322" width="75" height="23" rx="11" fill="#b9946c" role="img" aria-label="Top view of a wooden canoe with paddle"/>
    </g>

    <!-- dock photo portholes -->
    <g class="portholes">
      <circle cx="785" cy="89" r="63" fill="var(--ring)"/>
      <circle cx="785" cy="89" r="53" fill="url(#lake-day)" role="img" aria-label="Photo of a lake dock with a small boat and pine trees"/>
      <circle cx="941" cy="113" r="63" fill="var(--ring)"/>
      <circle cx="941" cy="113" r="53" fill="url(#lake-dusk)" role="img" aria-label="Photo of a fishing boat beside a dock at sunset"/>
      <circle cx="1107" cy="100" r="63" fill="var(--ring)"/>
      <circle cx="1107" cy="100" r="53" fill="url(#marina-blue)" role="img" aria-label="Photo of a canal marina with docked boats"/>
      <circle cx="805" cy="270" r="63" fill="var(--ring)"/>
      <circle cx="805" cy="270" r="53" fill="url(#shore-green)" role="img" aria-label="Photo of a floating dock by a wooded lakeshore"/>
      <circle cx="958" cy="262" r="63" fill="var(--ring)"/>
      <circle cx="958" cy="262" r="53" fill="url(#open-water)" role="img" aria-label="Photo of a boat lift dock on open water"/>
      <circle cx="1112" cy="269" r="63" fill="var(--ring)"/>
      <circle cx="1112" cy="269" r="53" fill="url(#palm-pier)" role="img" aria-label="Photo of a wooden pier with gazebo and palm trees"/>
    </g>

    <!-- bottom stripes -->
    <rect class="stripe-orange" x="0" y="361" width="1200" height="13" fill="var(--orange)"/>
    <g class="stripe-navy" fill="var(--navy)">
      <polygon points="19,385 993,385 984,406 9,406"/>
      <polygon points="1001,385 1023,385 1014,406 992,406"/>
      <polygon points="1030,385 1052,385 1043,406 1021,406"/>
      <polygon points="1058,385 1078,385 1069,406 1049,406"/>
      <polygon points="1101,385 1121,385 1112,406 1092,406"/>
      <polygon points="1134,385 1154,385 1145,406 1125,406"/>
      <polygon points="1167,385 1189,385 1180,406 1158,406"/>
    </g>
    <rect class="stripe-orange" x="0" y="417" width="1200" height="12" fill="var(--orange)"/>
  </svg>

  <div class="brand">
    <span class="brand-mark"></span>
    <span class="brand-name">Pierlend</span>
  </div>

  <div class="contact contact-email">
    <svg class="contact-icon" viewBox="0 0 24 24" aria-hidden="true">
      <path fill="#111" d="M6.6 10.8c1.4 2.8 3.8 5.1 6.6 6.6l2.2-2.2c.3-.3.7-.4 1-.2 1.1.4 2.3.6 3.6.6.6 0 1 .4 1 1V20c0 .6-.4 1-1 1C10.6 21 3 13.4 3 4c0-.6.4-1 1-1h3.5c.6 0 1 .4 1 1 0 1.3.2 2.5.6 3.6.1.3 0 .7-.2 1z"/>
      <path fill="none" stroke="#111" stroke-width="1.6" stroke-linecap="round" d="M14 6.5a4 4 0 0 1 3.5 3.5M14 3a7.5 7.5 0 0 1 7 7"/>
    </svg>
    <span>info@pierlend.example</span>
  </div>

  <div class="contact contact-phone">
    <svg class="contact-icon" viewBox="0 0 24 24" aria-hidden="true">
      <rect x="2" y="5" width="20" height="14" fill="#111"/>
      <path fill="none" stroke="var(--orange)" stroke-width="1.4" d="M2.5 5.5 12 13l9.5-7.5M2.5 18.5l7-6.5M21.5 18.5l-7-6.5"/>
    </svg>
    <span>+1 555 010 0188</span>
  </div>
</div>
</body>
</html>
```